Harvest Gateway Fellowship Ministries needs a fresh new web design

We are an up and coming multicultural church that aims to bring people into a life changing encounter with God. We need a fresh and inviting website in order to increase our internet presence and make us easier to connect with.
Here are some of the basic requirements for the site:
• Clearly displayed address, service times, and contact info
• A staff profile page
• An area for a calendar with upcoming events and their details
• Social media buttons
• Group pages for the different ministries (youth, children’s church, men, etc…)
• An area for donations and eCommerce
• A resources page for assorted media (podcasts, sermons, videos, etc.…)
• An area for prayer requests.

```html
<!DOCTYPE html>
<html lang="en">
<head>
<meta charset="utf-8">
<title>Harvest Gateway Fellowship Ministries</title>
<link href="https://fonts.googleapis.com/css2?family=Questrial&display=swap" rel="stylesheet">
<style>
:root{
  --orange:#e9a031;
  --blue:#0c5a8c;
  --navy:#1a4d7a;
  --text:#555a60;
  --line:#e3e3e3;
  --page:#f4f5f6;
  --red:#c3262c;
  --green:#7dbb2c;
}
*{box-sizing:border-box;margin:0;padding:0}
html,body{width:866px;height:1200px;overflow:hidden}
body{position:relative;background:#fff;font-family:"Questrial",sans-serif;color:var(--text);font-size:9px;line-height:1.8}
.abs{position:absolute}
.topband{left:0;top:0;width:866px;height:140px;background:var(--page)}
.contact-tab{left:500px;top:0;width:318px;height:34px;background:#fff;border-radius:0 0 8px 8px;box-shadow:0 1px 3px rgba(0,0,0,.15);display:flex;align-items:center;justify-content:center;gap:8px;color:var(--navy);font-size:12px}
.contact-tab svg{width:16px;height:14px}
.brand{left:62px;top:44px;display:flex;align-items:center;gap:6px;color:var(--navy);font-size:14px}
.brand i{width:16px;height:16px;border-radius:50%;background:var(--orange);display:block}
.nav{left:352px;top:76px;display:flex;font-size:10px;color:#222}
.nav a{display:block;padding:0 14px;height:24px;line-height:24px;text-decoration:none;color:#222}
.nav a.on{background:var(--orange);color:#fff;width:59px;text-align:center}
.hero{left:53px;top:110px;width:760px;height:301px;background:linear-gradient(120deg,#6b5e52,#3d3530 45%,#a08c72)}
.dots{left:69px;top:381px;display:flex;gap:6px}
.dots i{width:9px;height:9px;border-radius:50%;background:#fff;display:block}
.dots i:first-child{background:var(--orange)}
.prayer{left:606px;top:131px;width:186px;height:260px;background:#fff;box-shadow:0 1px 4px rgba(0,0,0,.3)}
.prayer h3{background:var(--blue);color:#fff;font-weight:400;font-size:13px;height:31px;line-height:31px;padding-left:13px}
.field{margin:10px 11px 0;height:23px;border:1px solid #ccc;font-size:8px;color:#888;padding:4px 10px}
.field+.field{margin-top:6px}
.field.msg{height:60px}
.btn{background:var(--orange);color:#fff;display:inline-block;font-size:10px;padding:0 7px;height:23px;line-height:23px}
.send{position:absolute;right:11px;bottom:10px;width:87px;text-align:center}
.card{border:1px solid var(--line);background:#fff}
.card h2{font-weight:400;font-size:16px;color:var(--navy);line-height:1}
.services .row{display:flex;justify-content:space-between;border-bottom:1px solid var(--line);height:21px;line-height:21px;padding:0 8px 0 1px}
.services .row span+span{color:var(--navy)}
.cal{left:270px;top:638px;width:202px;height:151px;background:#fff;box-shadow:0 2px 5px rgba(0,0,0,.25)}
.cal .head{background:var(--red);height:26px;color:#fff;font-size:11px;display:flex;align-items:center;justify-content:space-between;padding:0 18px}
.cal table{border-collapse:collapse;width:100%;text-align:center;font-size:8px;color:#333}
.cal th{font-weight:400;font-size:6px;color:#777;height:12px}
.cal td{border:1px solid #e4e6e8;height:22px;background:#f3f4f5}
.cal td.today{background:var(--green);color:#fff}
.tabs{left:53px;top:826px;width:566px;height:216px}
.tab{position:absolute;top:0;height:35px;line-height:35px;text-align:center;font-size:13px}
.tab.on{left:0;width:130px;background:#fff;color:var(--navy);border:1px solid var(--line);border-bottom:none;z-index:2;height:36px}
.tab.off{left:133px;width:130px;background:#7a7a7a;color:#fff}
.panel{position:absolute;left:0;top:35px;width:566px;height:181px;border:1px solid var(--line)}
.donate{left:638px;top:827px;width:175px;height:115px;background:linear-gradient(135deg,#0e3f6e,#2368a0);color:#fff}
.shop{left:638px;top:956px;width:175px;height:86px;background:linear-gradient(#f2f2f2,#dcdcdc)}
.footer{left:0;top:1061px;width:866px;height:139px;background:var(--blue);color:#fff;font-size:8.6px}
.footer h4{font-weight:400;color:var(--orange);font-size:11px;margin-bottom:2px}
.footer ul{list-style:none;line-height:15.5px}
.social li{display:flex;align-items:center;gap:8px;line-height:17.5px}
.social i{width:9px;height:9px;background:#d7e6f2;display:block;border-radius:2px}
.social li:last-child i{background:var(--orange)}
</style>
</head>
<body>
<div class="abs topband"></div>

<div class="abs contact-tab">
  <svg viewBox="0 0 16 16" aria-hidden="true"><rect x="1" y="1" width="14" height="14" rx="2" fill="#666"/><path d="M5 4c0 4 3 7 7 8l1-2-2-1-1 1c-1-.5-2-1.5-2.5-2.5l1-1-1-2z" fill="#fff"/></svg>
  <span>555.210.4480</span><span>&nbsp;|&nbsp;</span>
  <svg viewBox="0 0 18 14" aria-hidden="true"><rect x="1" y="1" width="16" height="12" fill="#777"/><path d="M1 1l8 7 8-7" stroke="#fff" fill="none"/></svg>
  <span>hello@harvestgateway.org</span>
</div>

<div class="abs brand"><i></i>HGFM</div>

<nav class="abs nav">
  <a class="on">HOME</a><a>ABOUT US</a><a>EVENTS</a><a>PRAYER REQUEST</a><a>DONATE</a><a>CONTACT US</a>
</nav>

<div class="abs hero" role="img" aria-label="Photo of a congregation seated in a worship hall listening to a speaker"></div>
<div class="abs dots"><i></i><i></i><i></i><i></i></div>

<form class="abs prayer">
  <h3>Prayer Requests</h3>
  <div class="field">Full Name</div>
  <div class="field">Email Address</div>
  <div class="field">Contact No.</div>
  <div class="field">Title</div>
  <div class="field msg">Message</div>
  <span class="btn send">SEND NOW</span>
</form>

<section class="abs card" style="left:53px;top:438px;width:436px;height:158px;padding:14px 13px">
  <h2>Welcome to HGFM</h2>
  <p style="margin-top:6px;line-height:15.3px">Welcome to Harvest Gateway Fellowship Ministries, a place where we can come together and fellowship. HGFM is located in Linden Falls, Ohio and we would love to have you worship with us. We believe God is doing something extraordinary through our church and would like for you to be a part. Please prayerfully consider our church as a place you would like to worship and fellowship with us as we continue to grow.</p>
  <span class="btn" style="margin-top:9px">Read More &rsaquo;&rsaquo;</span>
</section>

<section class="abs card services" style="left:508px;top:438px;width:305px;height:158px;padding:14px 15px 0 16px">
  <h2 style="margin-bottom:7px">Services Time</h2>
  <div class="row"><span>Aliquam molestie, mi et</span><span>Sunday&nbsp; 10:00am</span></div>
  <div class="row"><span>Imperdiet euismod</span><span>Sunday&nbsp; 10:00am</span></div>
  <div class="row"><span>Dui purus auctor tellus</span><span>Sunday&nbsp; 10:00am</span></div>
  <div class="row" style="border:none"><span>Nterdum lacus lectus et ante</span><span>Sunday&nbsp; 10:00am</span></div>
  <span class="btn" style="margin-top:3px">Read More &rsaquo;&rsaquo;</span>
</section>

<section class="abs card" style="left:53px;top:613px;width:436px;height:195px;padding:14px 13px">
  <h2>Upcoming Events</h2>
  <div style="color:var(--orange);margin-top:11px;font-size:9.5px">JUNE 10, 2014</div>
  <p style="width:190px;line-height:15.3px">Aliquam molestie, mi et imperdiet euismod, dui purus auctor tellus, et interdum lacus lectus et ante....</p>
  <div style="color:var(--navy);margin-top:6px">Read More &rsaquo;&rsaquo;</div>
  <span class="btn" style="margin-top:16px;padding:0 10px">View all Events &rsaquo;&rsaquo;</span>
</section>

<div class="abs cal">
  <div class="head"><span>&#9664;</span><span>JUNE 2014</span><span>&#9654;</span></div>
  <table>
    <tr><th>SUN</th><th>MON</th><th>TUE</th><th>WED</th><th>THU</th><th>FRI</th><th>SAT</th></tr>
    <tr><td>1</td><td>2</td><td>3</td><td>4</td><td>5</td><td>6</td><td>7</td></tr>
    <tr><td>8</td><td>9</td><td class="today">10</td><td>11</td><td>12</td><td>13</td><td>14</td></tr>
    <tr><td>15</td><td>16</td><td>17</td><td>18</td><td>19</td><td>20</td><td>21</td></tr>
    <tr><td>22</td><td>23</td><td>24</td><td>25</td><td>26</td><td>27</td><td>28</td></tr>
    <tr><td>29</td><td>30</td><td>31</td><td></td><td></td><td></td><td></td></tr>
  </table>
</div>

<section class="abs card" style="left:508px;top:613px;width:305px;height:195px;padding:14px 15px">
  <h2>Staff Profile</h2>
  <div class="abs" role="img" aria-label="Portrait of a staff member in a suit seated at an office desk" style="left:16px;top:42px;width:122px;height:101px;background:linear-gradient(135deg,#8a7f6e,#3b3530)"></div>
  <p class="abs" style="left:151px;top:38px;width:145px;line-height:15.4px">Aliquam molestie, mi et imperdiet euismod, dui purus auctor tellus, et interdum lacus lectus et ante. Sed accumsan sollicitudin sapien, sit amet adipiscing turpis gravida ac. Vivamus egestas risus in magna varius commodo.</p>
  <span class="btn abs" style="left:151px;top:155px">View Staff Profile &rsaquo;&rsaquo;</span>
</section>

<section class="abs tabs">
  <div class="tab on">Our Group</div>
  <div class="tab off">Resources</div>
  <div class="panel">
    <div class="abs" role="img" aria-label="Group photo of ministry members standing together indoors" style="left:17px;top:28px;width:158px;height:132px;background:linear-gradient(135deg,#c9b9a8,#7c6a5c)"></div>
    <p class="abs" style="left:192px;top:24px;width:350px;line-height:15.4px">Aliquam molestie, mi et imperdiet euismod, dui purus auctor tellus, et interdum lacus lectus et ante. Sed accumsan sollicitudin sapien, sit amet adipiscing turpis gravida ac. In congue, neque ac lobortis volutpat, libero mauris varius mi, vitae suscipit ipsum ligula vitae risus. Duis aliquam nibh a dui iaculis viverra id a velit. Vivamus egestas risus in magna varius commodo. Sed semper viverra egestas. Etiam pretium porttitor lectus, vel ornare neque porta volutpat.</p>
    <span class="btn abs" style="left:192px;top:138px">Read More &rsaquo;&rsaquo;</span>
  </div>
</section>

<aside class="abs donate">
  <div class="abs" role="img" aria-label="Paper cup holding banknotes and coins" style="left:16px;top:34px;width:95px;height:75px;background:radial-gradient(ellipse at center,#c8d2dc,rgba(200,210,220,0) 70%)"></div>
  <div class="abs" style="right:9px;top:6px;font-size:21px;letter-spacing:1px">DONATE</div>
  <div class="abs" style="right:11px;top:36px;font-size:8px;color:var(--orange)">WITH</div>
  <div class="abs" style="right:9px;top:52px;width:67px;height:18px;border-radius:9px;background:var(--orange);color:var(--navy);font-size:8px;text-align:center;line-height:18px">QuickGive</div>
</aside>

<aside class="abs shop" role="img" aria-label="Online shop banner: click here to shop now"></aside>

<footer class="abs footer">
  <div class="abs" style="left:56px;top:44px;display:flex;align-items:center;gap:6px;font-size:14px"><i style="width:16px;height:16px;border-radius:50%;background:var(--orange);display:block"></i>HGFM</div>
  <div class="abs" style="left:55px;top:96px;line-height:15.5px;color:#dce8f1">&copy; 2014 HGFM. All Rights Reserved |&nbsp; Privacy Policy<br>Terms Conditions | Sitemap</div>
  <div class="abs" style="left:465px;top:18px">
    <h4>Quick Links</h4>
    <ul><li>Home</li><li>About Us</li><li>Events</li><li>Prayer Request</li><li>Donate</li><li>Contact Us</li></ul>
  </div>
  <div class="abs" style="left:575px;top:18px">
    <h4>Connect Us</h4>
    <ul class="social"><li><i></i>Friendbook</li><li><i></i>Chirper</li><li><i></i>LinkUp</li><li><i></i>ViewTube</li><li><i></i>Rss Feeds</li></ul>
  </div>
  <div class="abs" style="left:699px;top:18px;width:130px;line-height:13.5px">
    <h4 style="margin-bottom:4px">Contact Us</h4>
    <div style="font-size:9.5px">Company Name</div>
    <div>1420 Orchard Lane, Brookvale, BV4 2KR.</div>
    <div style="margin-top:3px">Phone: <span style="color:var(--orange);font-size:10px">555.210.4480</span></div>
    <div>Email: hello@harvestgateway.org</div>
  </div>
</footer>
</body>
</html>
```